Storm Restoration Contractor needs a professional letterhead design

Looking for a professional letterhead design. Not looking for your cheapo MS Word standard ones that are readily available. Dont want it to be cookie cutter look like ones readily available online. We just recently changed our logo and want to freshen up all our documents. Our company handles restoring a property back to a pre-loss condition after a storm damages it. For example, wind, hail, flood, fire losses.

Target Market(s)

Property Owners, Homeowners, Property Owners, Commercial Property Owners, Property Management Companies

Industry/Entity Type

Construction Company

Requirements
Must have
• Professional, Use 1 of 2 logo options
• Storm Restoration, Roofing, Siding, Windows

```html
<!DOCTYPE html>
<html lang="en">
<head>
<meta charset="utf-8">
<title>Stonebrook Exteriors — Letterhead</title>
<link rel="stylesheet" href="https://fonts.googleapis.com/css2?family=Questrial&display=swap">
<style>
  :root {
    --backdrop: #bdbdbd;
    --paper: #f1f1f1;
    --brand-blue: #2a6ab3;
    --brand-grey: #4a4a4a;
    --text: #3c3c3c;
  }
  * { box-sizing: border-box; margin: 0; padding: 0; }
  html, body {
    width: 1200px;
    height: 1041px;
    overflow: hidden;
    background: var(--backdrop);
    font-family: "Questrial", sans-serif;
  }
  .letterhead {
    position: absolute;
    left: 213px;
    top: 20px;
    width: 774px;
    height: 1001px;
    background: var(--paper);
    overflow: hidden;
  }
  .masthead {
    position: absolute;
    top: 52px;
    left: 0;
    width: 100%;
    display: flex;
    justify-content: center;
    align-items: center;
    gap: 12px;
  }
  .masthead__mark {
    width: 58px;
    height: 58px;
    border-radius: 50%;
    background: var(--brand-blue);
  }
  .masthead__divider {
    width: 2px;
    height: 66px;
    background: var(--brand-blue);
  }
  .masthead__name {
    color: var(--brand-blue);
    font-size: 25px;
    line-height: 1.05;
    letter-spacing: 2px;
    text-transform: uppercase;
  }
  .footer {
    position: absolute;
    top: 940px;
    left: 0;
    width: 100%;
    text-align: center;
    color: var(--text);
    font-size: 10.5px;
    line-height: 14px;
  }
  .footer__label, .footer__domain { color: var(--brand-blue); font-weight: bold; }
  .base-band { position: absolute; left: 0; bottom: 0; }
</style>
</head>
<body>
  <main class="letterhead">
    <header class="masthead">
      <div class="masthead__mark"></div>
      <div class="masthead__divider"></div>
      <div class="masthead__name">Stonebrook<br>Exteriors</div>
    </header>

    <footer class="footer">
      <p class="footer__address">4120 N Canyon Ridge Road STE 210, Mesa, AZ 85201</p>
      <p class="footer__contact">
        <span class="footer__label">T:</span> 555-010-4400 ·
        <span class="footer__label">F:</span> 555-010-4400 ·
        <span class="footer__label">E:</span> info@stonebrookext.com ·
        www.<span class="footer__domain">stonebrookext</span>.com
      </p>
    </footer>

    <svg class="base-band" width="774" height="20" viewBox="0 0 774 20" aria-hidden="true">
      <rect x="0" y="9" width="774" height="11" fill="var(--brand-grey)"/>
      <polygon points="68,20 80,2 697,2 710,20" fill="#ffffff"/>
      <polygon points="72,20 84,2 692,2 705,20" fill="var(--brand-blue)"/>
    </svg>
  </main>
</body>
</html>
```